We need letterhead, Business Cards, and envelops designed. We have attached a design of our logo and a sample of letterhead idea that was started but never perfected, it is only an idea for the letterhead if you can design something better we may love that also we are open to change.
We want a design that looks professional in style. we are a non profit trade association in the construction industry. the green color in the attached design represent green building, and we like that. also if you just want to enhance the letterhead sample that we attached that would be fine also.
Thanks and good luck
also the name that should show on the first business cards should be Morgan Feltwick, Director are web address is www.pvtrn.org

```html
<!DOCTYPE html>
<html lang="en">
<head>
<meta charset="utf-8">
<title>PVTRN Letterhead</title>
<link href="https://fonts.googleapis.com/css2?family=Arimo:wght@400;700&display=swap" rel="stylesheet">
<style>
  :root {
    --backdrop: #e4e5e6;
    --paper: #ffffff;
    --ink: #1c1c1c;
    --ink-soft: #8a8a8a;
    --green: #6f9a3a;
    --green-pale: #dfe8d6;
    --band: #0d0d0d;
    --band-text: #e9e9e9;
  }
  * { box-sizing: border-box; margin: 0; padding: 0; }
  html, body { width: 1200px; height: 909px; overflow: hidden; }
  body {
    background: var(--backdrop);
    font-family: "Arimo", Arial, sans-serif;
    color: var(--ink);
    position: relative;
  }
  .letterhead {
    position: absolute;
    left: 270px; top: 26px;
    width: 660px; height: 856px;
    background: var(--paper);
    box-shadow: 0 4px 18px rgba(0,0,0,0.12);
    overflow: hidden;
  }
  .sender-contact {
    position: absolute;
    right: 56px; top: 42px;
    text-align: right;
    font-size: 7.5px;
    line-height: 1.45;
    letter-spacing: 0.8px;
    color: var(--ink-soft);
  }
  .sender-contact .gap { height: 6px; }
  .sender-contact .dot {
    display: inline-block; width: 5px; height: 5px;
    background: var(--green); border-radius: 50%;
    margin-left: 5px; vertical-align: middle;
  }
  .brand {
    position: absolute;
    left: 50px; top: 150px;
    display: flex; align-items: center; gap: 8px;
  }
  .brand-mark {
    width: 14px; height: 14px; background: var(--green);
  }
  .brand-name {
    font-size: 40px; font-weight: 700; letter-spacing: 2px;
    color: var(--ink); line-height: 1;
  }
  .brand-tagline {
    position: absolute; left: 50px; top: 196px;
    font-size: 8px; letter-spacing: 0.6px; color: var(--ink);
    border-top: 2px solid var(--ink); padding-top: 3px;
  }
  .decoration {
    position: absolute; left: 140px; bottom: 44px;
    width: 340px; height: 250px;
  }
  .letter {
    position: absolute;
    left: 56px; top: 250px; width: 548px;
    font-size: 9px; line-height: 1.42;
  }
  .recipient { margin-bottom: 12px; }
  .salutation { margin-bottom: 10px; }
  .letter p.body { margin-bottom: 10px; }
  .closing { margin-top: 26px; }
  .signer { margin-top: 36px; }
  .footer-band {
    position: absolute; left: 0; bottom: 0;
    width: 100%; height: 44px; background: var(--band);
    display: flex; align-items: center; justify-content: flex-end;
    padding-right: 56px;
  }
  .web-address {
    color: var(--band-text); font-size: 11px; letter-spacing: 3px;
  }
</style>
</head>
<body>
  <main class="letterhead">
    <address class="sender-contact">
      Address<br>
      4321 first street<br>
      Anytown, State ZIP
      <div class="gap"></div>
      123-456-7890<span class="dot"></span><br>
      123-456-7891<span class="dot"></span>
    </address>

    <div class="brand">
      <span class="brand-name">PVTRN</span>
      <span class="brand-mark"></span>
    </div>
    <div class="brand-tagline">Pacific Valley Trade Network</div>

    <svg class="decoration" viewBox="0 0 340 250" role="img" aria-label="Faint green building decoration">
      <rect x="0" y="0" width="340" height="250" fill="var(--green-pale)" opacity="0.8"/>
    </svg>

    <section class="letter">
      <div class="recipient">
        June 26, 2014<br>
        Trenz Pruca<br>
        Title<br>
        Company Name<br>
        4321 First Street<br>
        Anytown, State ZIP
      </div>
      <p class="salutation">Dear Trenz,</p>
      <p class="body">Lorem ipsum dolor sit amet, consectetur adipiscing elit, sed eiusmod tempor incidunt et labore et dolore magna aliquam. Ut enim ad minim veniam, quis nostrud exerc. Irure dolor in reprehend incididunt ut labore et dolore magna aliqua. Ut enim ad minim veniam, quis nostrud exercitation ullamco laboris nisi ut aliquip ex ea commodo consequat. Duis aute irure dolor in reprehenderit in voluptate velit esse molestaie cillum. Tia non ob ea soluad incom dereud facilis est er expedit distinct. Nam liber te conscient to factor tum poen legum odioque civiuda et tam.</p>
      <p class="body">At vver eos et accusam dignissum qui blandit est praesent. Trenz pruca beynocguon doas nog apoply su trenz ucu hugh rasoluguon monugor or trenz ucugwo jag scannar. Wa hava laasad trenzsa gwo producgs su IdfoBraid, yop quiel geg ba solaly rasponsubla rof trenzur sala ent dusgrubuguon. Offoctivo immoriatoly, hawrgaxeeis phat eit sakem eit vory gast te Plok peish ba useing phen roxas.</p>
      <p class="body">Plloaso mako nuto uf cakso dodtos anr koop a cupy uf cak vux noaw yerw phuno. Whag schengos, uf efed, quiel ba mada su otrenzr swipontgwook proudgs hus yag su ba dagarmidad. Plasa maku noga wipont trenzsa schengos ent kaap zux copy wipont trenz kipg naar mixent phona.</p>
      <p class="body">Lorem ipsum dolor sit amet, consectetur adipiscing elit. Donec id erat quis metus suscipit mattis. Duis elit elit, venenatis id ullamcorper at, sollicitudin nec eros. Vivamus ultricies dapibus neque ut laoreet. Suspendisse massa est, fringilla quis neque a, semper consequat lacus. Etiam imperdiet dignissim nibh placerat condimentum convallis quis a lacus.</p>
      <p class="closing">Sincerely yours,</p>
      <p class="signer">Urna Semper</p>
    </section>

    <footer class="footer-band">
      <span class="web-address">www.pvtrn.org</span>
    </footer>
  </main>
</body>
</html>
```